Allied Health team of Physiotherapists & Occupational Therapists seek a business card design

We have our new logo, we now need our new business cards and stationary. Tidewell: Oedema & Family Clinic is seeking a generic card design to represent our whole team and individual cards for each therapist that incorporates our new logo to communicate our holistic approach that is calming, nuturing, supportive and welcoming.
Our Physiotherapists and Occupational Therapists assess, treat and provide education for people who are at risk of or who have lymphoedema. This is often as a result of treatment for cancer. We provide pre-operative and post-operative management and cancer rehabilitation in our Pilates studio. Our team also consists of Physiotherapists who have a strong interest in pelvic floor and continence management for both men and women.

Target Market(s)

Mainly women health conscious

Industry/Entity Type

Allied Health: Physiotherapy / Occupational Therapy

Contact Information for Business Card

Address: 14 Gallivant Ave Frankston 3199 Phone: 84316570 fax: 8431 6578 Email: info@tidewellcareservices.com.au Website: tidewellcareservices.com.au Facebook address: facebook.com/TidewellOedemaAndFamilyCareClinic. Room to write appointments. Individual cards need to have name, office email and individual email and professional details

Requirements
Must have
• Logo as per uploaded documents

```html
<!DOCTYPE html>
<html lang="en">
<head>
<meta charset="utf-8">
<title>Tidewell Oedema &amp; Family Clinic – Business Card</title>
<link rel="stylesheet" href="https://fonts.googleapis.com/css2?family=Open+Sans:wght@400;600;700&display=swap">
<style>
  :root {
    --peach: #f9b089;
    --sage: #c9d3cb;
    --ink: #2b2b2b;
    --ink-soft: #4a4a4a;
    --paper: #ffffff;
    --backdrop: #ece8e4;
  }
  * { box-sizing: border-box; margin: 0; padding: 0; }
  html, body { width: 1200px; height: 913px; overflow: hidden; }
  body {
    background: var(--backdrop);
    font-family: "Open Sans", Arial, sans-serif;
    position: relative;
  }
  .card {
    position: absolute;
    width: 620px;
    height: 354px;
    box-shadow: 0 10px 28px rgba(0,0,0,0.18);
    overflow: hidden;
  }

  /* Back of card */
  .card-back {
    left: 60px; top: 60px;
    background: var(--peach);
    color: var(--paper);
  }
  .back-brand {
    position: absolute;
    left: 0; right: 0; top: 88px;
    display: flex; flex-direction: column; align-items: center;
  }
  .brand-dot {
    width: 14px; height: 14px; border-radius: 50%;
    background: var(--paper);
    margin-bottom: 12px;
  }
  .brand-name {
    font-size: 30px; font-weight: 600; letter-spacing: 1px; line-height: 1.1;
  }
  .brand-sub {
    font-size: 30px; font-weight: 600; letter-spacing: 1px; line-height: 1.1;
    font-size: 14px; margin-top: 6px; letter-spacing: 2px; text-transform: uppercase;
  }
  .back-web {
    position: absolute;
    left: 0; right: 0; bottom: 58px;
    text-align: center;
    font-size: 17px;
    letter-spacing: 4px;
  }

  /* Front of card */
  .card-front {
    left: 520px; top: 500px;
    background: var(--paper);
    color: var(--ink);
  }
  .front-bands { position: absolute; left: 0; top: 0; }
  .front-brand {
    position: absolute;
    right: 40px; top: 84px;
    width: 200px;
    text-align: center;
    color: var(--peach);
  }
  .front-brand .brand-name { font-size: 24px; }
  .front-brand .brand-sub { font-size: 10px; }
  .person {
    position: absolute; left: 118px; top: 92px;
  }
  .person-name { font-size: 18px; font-weight: 700; letter-spacing: 0.5px; line-height: 1.1; }
  .person-role { font-size: 11.5px; color: var(--ink-soft); }
  .contact-list {
    position: absolute; left: 22px; bottom: 36px;
    list-style: none;
  }
  .contact-list li, .address {
    display: flex; align-items: center; gap: 8px;
    font-size: 12px; color: var(--ink);
    margin-top: 6px;
  }
  .icon {
    width: 18px; height: 18px; border-radius: 50%;
    background: var(--ink);
    display: inline-flex; align-items: center; justify-content: center;
    flex: none;
  }
  .address {
    position: absolute; right: 40px; top: 210px;
    align-items: flex-start; line-height: 1.35;
  }
</style>
</head>
<body>

  <section class="card card-back" aria-label="Card back">
    <div class="back-brand">
      <span class="brand-dot"></span>
      <span class="brand-name">Tidewell</span>
      <span class="brand-sub">Oedema &amp; Family Clinic</span>
    </div>
    <p class="back-web">www.tidewellcareservices.com.au</p>
  </section>

  <section class="card card-front" aria-label="Card front">
    <svg class="front-bands" width="620" height="354" viewBox="0 0 620 354" aria-hidden="true">
      <rect x="360" y="0" width="260" height="56" fill="var(--sage)"/>
      <path d="M0 0 H372 Q386 0 386 14 V54 Q386 70 370 70 H0 Z" fill="var(--peach)"/>
      <rect x="0" y="96" width="100" height="34" fill="var(--sage)"/>
    </svg>

    <div class="front-brand">
      <span class="brand-name">Tidewell</span><br>
      <span class="brand-sub">Oedema &amp; Family Clinic</span>
    </div>

    <div class="person">
      <p class="person-name">HANNAH LOWRY</p>
      <p class="person-role">Principal Physiotherapist</p>
    </div>

    <ul class="contact-list">
      <li>
        <span class="icon"><svg width="10" height="10" viewBox="0 0 24 24"><path fill="#fff" d="M6.6 10.8a15 15 0 0 0 6.6 6.6l2.2-2.2a1 1 0 0 1 1-.25 11.4 11.4 0 0 0 3.6.6 1 1 0 0 1 1 1V20a1 1 0 0 1-1 1A17 17 0 0 1 3 4a1 1 0 0 1 1-1h3.5a1 1 0 0 1 1 1c0 1.25.2 2.45.6 3.6a1 1 0 0 1-.25 1z"/></svg></span>
        8431 6570
      </li>
      <li>
        <span class="icon"><svg width="10" height="10" viewBox="0 0 24 24"><path fill="#fff" d="M12 3 2 12h3v8h5v-6h4v6h5v-8h3z"/></svg></span>
        8431 6578
      </li>
      <li>
        <span class="icon"><svg width="10" height="10" viewBox="0 0 24 24"><path fill="#fff" d="M3 5h18v14H3zm2 2v.5l7 4.5 7-4.5V7z"/></svg></span>
        hannah@tidewellcareservices.com.au
      </li>
    </ul>

    <div class="address">
      <span class="icon"><svg width="10" height="10" viewBox="0 0 24 24"><path fill="#fff" d="M12 2a7 7 0 0 0-7 7c0 5 7 13 7 13s7-8 7-13a7 7 0 0 0-7-7zm0 9.5A2.5 2.5 0 1 1 12 6.5a2.5 2.5 0 0 1 0 5z"/></svg></span>
      <span>14 Gallivant Ave<br>Frankston VIC 3199</span>
    </div>
  </section>

</body>
</html>
```